Veldmark Supplies Business Card

Professional business card that stand out to our potential customers. Front and back with clean modern design

Industry/Entity Type

Oil and gas

Contact Information for Business Card

Name, address, website , office phone and cell number

Requirements
Must have
• Editable files for each employee

```html
<!DOCTYPE html>
<html lang="en">
<head>
<meta charset="utf-8">
<title>Veldmark Supplies – Business Card</title>
<link href="https://fonts.googleapis.com/css2?family=Poppins:wght@400;600&display=swap" rel="stylesheet">
<style>
  :root{
    --bg:#e3e7e9;
    --card-dark:#222226;
    --card-light:#ffffff;
    --red:#e8262a;
    --cyan:#14afd1;
    --ink:#1d1d1f;
  }
  *{margin:0;padding:0;box-sizing:border-box}
  html,body{width:1200px;height:960px;overflow:hidden;background:var(--bg);font-family:"Poppins",sans-serif}
  .card{position:absolute;left:250px;width:701px;height:400px;border-radius:33px;overflow:hidden}
  .card-front{top:60px;background:var(--card-dark)}
  .card-back{top:500px;background:var(--card-light)}

  .brand{position:absolute;display:flex;align-items:center;gap:12px;color:var(--red);font-weight:600;white-space:nowrap}
  .brand-mark{display:block;background:var(--cyan)}
  .card-front .brand{left:0;right:0;top:178px;justify-content:center;font-size:34px;letter-spacing:2px}
  .card-front .brand-mark{width:30px;height:30px}
  .card-back .brand{right:28px;top:90px;font-size:21px;letter-spacing:1px}
  .card-back .brand-mark{width:18px;height:18px}

  .name-bar{position:absolute;left:0;top:163px;width:21px;height:52px;background:var(--cyan)}
  .person-name{position:absolute;left:27px;top:157px;font-size:34px;line-height:1.2;white-space:nowrap}
  .person-name .first{color:var(--red);font-weight:600}
  .person-name .last{color:var(--cyan);font-weight:400}
  .person-title{position:absolute;left:27px;top:194px;font-size:17px;color:var(--ink)}
  .divider{position:absolute;left:210px;right:0;top:208px;height:2px;background:var(--cyan)}

  .address{position:absolute;right:26px;top:218px;text-align:right;color:var(--red);font-size:17.5px;line-height:24px}
  .contacts{position:absolute;right:26px;top:280px;list-style:none;text-align:right;color:var(--ink);font-size:18.5px;line-height:24.3px}
  .contacts li{display:flex;justify-content:flex-end;align-items:center;gap:10px}
  .contacts svg{width:16px;height:16px;flex:none}
</style>
</head>
<body>
  <section class="card card-front">
    <div class="brand"><span class="brand-mark"></span>VELDMARK SUPPLIES</div>
  </section>

  <section class="card card-back">
    <div class="brand"><span class="brand-mark"></span>VELDMARK SUPPLIES</div>

    <div class="name-bar"></div>
    <h1 class="person-name"><span class="first">Marta</span> <span class="last">Oleskova</span></h1>
    <p class="person-title">Co-Founder &amp; CEO</p>
    <div class="divider"></div>

    <p class="address">1840 Cedar Ridge Ave. Suite 300<br>Lubbock, TX 79401</p>

    <ul class="contacts">
      <li>(806) 412-5530
        <svg viewBox="0 0 16 16"><path d="M3 1.5l2.5-.5 1.5 3.5-1.7 1.2c.8 1.8 2.2 3.2 4 4l1.2-1.7 3.5 1.5-.5 2.5c-6 .8-11.3-4.5-10.5-10.5z" fill="var(--cyan)"/></svg>
      </li>
      <li>(555) 310-4471
        <svg viewBox="0 0 16 16"><rect x="4" y="1" width="8" height="14" rx="1.5" fill="none" stroke="var(--red)" stroke-width="1.6"/></svg>
      </li>
      <li>www.veldmark.co
        <svg viewBox="0 0 16 16"><circle cx="8" cy="8" r="7" fill="var(--cyan)"/><path d="M1 8h14M8 1c3 3 3 11 0 14M8 1c-3 3-3 11 0 14" fill="none" stroke="#fff" stroke-width="1"/></svg>
      </li>
      <li>hello@veldmark.co
        <svg viewBox="0 0 16 16"><rect x="1" y="4" width="14" height="10" rx="1" fill="var(--red)"/><path d="M1 4l7 6 7-6" fill="none" stroke="#fff" stroke-width="1.2"/></svg>
      </li>
    </ul>
  </section>
</body>
</html>
```